Business Card Design Project - del varosi group

dear Sirs

we need business card design for our group ( DEL Varosi Group ) , i have got the Logo design of our group from pixel harbor in previous , so all need details relating to our group i think available with you, as well as the the chosen logo design

we hope to provide us with business card logo that to be appropaite and satisfactory to us .

thanks

note : logo design of our group is attached .
Updates

Reason: please extend the deadline of my project for additional 15 days because i didn't received appropriate design for our gruop yet . kindly beaware that i have received 77 design till now , supossed to send me 200-250 design at least . thanks

Target Market(s)

contents

name : Kerem EL Nadiri

position : Operation Manager

Industry/Entity Type

Business

Requirements
Must have

• person name

group logo
Nice to have
• logo color matching with back background

```html
<!DOCTYPE html>
<html lang="en">
<head>
<meta charset="utf-8">
<title>DEL Varosi Group – Business Card</title>
<link rel="stylesheet" href="https://fonts.googleapis.com/css2?family=Open+Sans:wght@400;600&display=swap">
<style>
  :root {
    --bg: #efe9d6;
    --navy-light: #1f4a8a;
    --navy: #163a73;
    --navy-dark: #0e2b5a;
    --gold: #d7ad3e;
    --gold-light: #edcb63;
    --gold-dark: #c8982a;
    --card-white: #ffffff;
    --ink: #0f2b5c;
  }
  * { box-sizing: border-box; margin: 0; padding: 0; }
  html, body { width: 1200px; height: 951px; overflow: hidden; }
  body {
    background: var(--bg);
    font-family: "Open Sans", Arial, sans-serif;
    position: relative;
  }
  .card {
    position: absolute;
    width: 580px;
    height: 330px;
    border-radius: 24px;
    overflow: hidden;
    box-shadow: 0 10px 24px rgba(60, 50, 20, 0.22);
  }
  /* Front */
  .card-front {
    left: 110px; top: 100px;
    background: radial-gradient(ellipse at 45% 40%, var(--navy-light), var(--navy) 55%, var(--navy-dark));
  }
  .brand {
    position: absolute;
    left: 0; right: 0; top: 112px;
    display: flex; align-items: center; justify-content: center; gap: 16px;
  }
  .brand-mark {
    width: 34px; height: 34px;
    background: var(--gold);
  }
  .brand-name {
    color: #ffffff;
    font-weight: 600;
    font-size: 40px;
    letter-spacing: 0.5px;
  }
  .front-web {
    position: absolute;
    left: 0; right: 0; top: 222px;
    text-align: center;
    color: var(--gold);
    font-size: 19px;
    letter-spacing: 1.5px;
  }
  /* Back */
  .card-back {
    left: 510px; top: 520px;
    background: var(--card-white);
  }
  .info-band {
    position: absolute;
    left: 0; right: 0; top: 72px; height: 210px;
    display: flex;
  }
  .identity {
    width: 40%;
    background: linear-gradient(135deg, var(--navy-light), var(--navy-dark));
    display: flex; flex-direction: column; justify-content: center;
    padding-left: 34px;
  }
  .person-name { color: var(--gold); font-size: 22px; font-weight: 400; }
  .person-role { color: #ffffff; font-size: 16px; margin-top: 4px; }
  .contacts {
    flex: 1;
    position: relative;
    background: linear-gradient(100deg, var(--gold-dark), var(--gold-light) 50%, var(--gold));
    padding: 18px 0 0 46px;
    color: var(--ink);
    font-size: 15.5px;
    line-height: 1.3;
  }
  .contacts::before {
    content: "";
    position: absolute;
    left: 18px; top: 22px; bottom: 22px;
    width: 1px;
    background: rgba(255, 255, 255, 0.6);
  }
  .contact-line { display: flex; align-items: flex-start; gap: 10px; }
  .contact-line + .contact-line { margin-top: 2px; }
  .address { margin-bottom: 10px; }
  .icon { width: 14px; height: 14px; flex: none; margin-top: 3px; fill: var(--ink); }
</style>
</head>
<body>
  <section class="card card-front" aria-label="Business card front">
    <div class="brand">
      <span class="brand-mark"></span>
      <span class="brand-name">DEL Varosi Group</span>
    </div>
    <p class="front-web">www.delvarosigroup.com</p>
  </section>

  <section class="card card-back" aria-label="Business card back">
    <div class="info-band">
      <div class="identity">
        <p class="person-name">Kerem EL Nadiri</p>
        <p class="person-role">Operation Manager</p>
      </div>
      <div class="contacts">
        <div class="contact-line address">
          <svg class="icon" viewBox="0 0 14 14"><path d="M7 1 L13 6.5 H11 V13 H8.3 V9 H5.7 V13 H3 V6.5 H1 Z"/></svg>
          <span>4150 Lark Hollow Rd.<br>Suite 210-118<br>Marston, TX 78114</span>
        </div>
        <div class="contact-line">
          <svg class="icon" viewBox="0 0 14 14"><path d="M3 1 L5.5 1 L6.5 4 L5 5.2 C5.8 7 7 8.2 8.8 9 L10 7.5 L13 8.5 V11 C13 12 12 13 11 13 C5.5 12.5 1.5 8.5 1 3 C1 2 2 1 3 1 Z"/></svg>
          <span>512-555-0142</span>
        </div>
        <div class="contact-line">
          <svg class="icon" viewBox="0 0 14 14"><rect x="3" y="1" width="8" height="4"/><rect x="1" y="5" width="12" height="6" rx="1"/><rect x="3" y="9" width="8" height="4" fill="#fff"/></svg>
          <span>512-555-0143</span>
        </div>
        <div class="contact-line">
          <svg class="icon" viewBox="0 0 14 14"><rect x="1" y="3" width="12" height="8" rx="1"/><path d="M1.5 3.5 L7 8 L12.5 3.5" stroke="#fff" stroke-width="1.2" fill="none"/></svg>
          <span>info@delvarosigroup.com</span>
        </div>
        <div class="contact-line">
          <svg class="icon" viewBox="0 0 14 14"><circle cx="7" cy="7" r="6"/></svg>
          <span>www.delvarosigroup.com</span>
        </div>
      </div>
    </div>
  </section>
</body>
</html>
```